Women's Jewellery startup needs a captivating, beautifully designed and intuitive online store

[12/24 update]

Added 2 additional documents:

Feedback on designs received so far: designer feedback.docx
Product images from catalogue: products images.docx

Please read the feedback provided on designs provided so far to guide you further on your submission. The product images can be used to create promotional banners for the site.

@@@Added a document (VELISTO JEWELLERY_checklist.docx) which can be used by designers as a checklist when submitting their designs to ensure all aspects of the requirements have been covered @@@

+++IMPORTANT BUT NOT SPECIFIED IN THE REQUIREMENTS DOCUMENT - DESIGN SHOULD INCLUDE SUPPORT FOR MOBILE FRIENDLY SITE TOO+++

***Previous experience designing Jewellery online stores preferred (not essential)***

The name of the online Jewellery store is "Velisto Jewellery" and the business is based in Hong Kong. It will be run by 2 stay at home mothers. We need a Shopify themed store designed that will achieve the following objectives in order of priority:

• Conversion: The primary objective of the design/content is to prompt the customer to make a purchase. While this may sound obvious, it is mentioned so as not to distract the design process by focusing on other objectives (which are also important). The site also needs to be optimized so as to rank high in search engine searches for relevant keywords (SEO)
• Navigation: An intuitive interface which takes away a lot of the thinking from the customer by making it obvious what they need to do when they visit the store
• Engagement: Encourages the customer to spend time on the website and share content with their social network

Where applicable, the design of the store should reflect as closely as possible the mission statements and words outlined below:

• Jewellery you’ll fall in love with
• We want every client to leave the store with a smile
• We want to be able to provide the best service we can in every situation no matter what
• We aim to increase our business by word of mouth; therefore we tell people things about our store that makes it interesting for them to share
• We love every customer, no matter how difficult things get
• We, as a team, are so well informed about our products and brands that we always have the best information for our customers
• We celebrate women here!
• We celebrate life in here!
• We celebrate beauty here!
• We celebrate families here, as jewellery often stays within families.
• We will always try to make an extra step
• We will always try to exceed the expectation of our customers
• We will go as far as we possibly can to attract a customer back to our store and connect with us
• Every client that leaves our store knows more about jewellery because we passionately told him about it
• Romantic, classic, love, warm, cool, stylish

A draft functional specification is attached with this brief. We would like the design to reflect as closely as possible the functional requirements outlined in the document. Open to suggestions to improve upon the functional requirements.

Target Market(s)

Women aged 18-55

Industry/Entity Type

Jewelry Store

Coding

Coded - Design and coding required

Number of Pages Required

5+ page

Font styles to use
Other font styles liked:
• Myriad Pro as per Logo but open to any font that complements this one

Requirements
Must have
• 1. A look that encourages the user to make a purchase
• 2. An intuitive, easy to navigate and engaging interface
• 3. Primary colour scheme as defined in the functional specification attached
• 4. Simplistic look, not too cluttered
Nice to have
• 1. Closely matching the functional requirements of the site as outlined in the requirements specification but open to any better ideas

```html
<!DOCTYPE html>
<html lang="en">
<head>
<meta charset="utf-8">
<title>Velisto Jewellery – Shop</title>
<link href="https://fonts.googleapis.com/css2?family=Bebas+Neue&family=Oxygen:wght@400;700&family=Montserrat:wght@400;600;700&family=Cinzel:wght@400&display=swap" rel="stylesheet">
<style>
:root{
  --ink:#111;
  --bar:#0c0c0c;
  --nav:#f4f1ec;
  --gold:#c69a4f;
  --rust:#b9532c;
  --cream:#faf7f2;
  --line:#e3ddd3;
  --text:#555;
  --footer:#1a1a1a;
  --veil:rgba(0,0,0,.84);
}
*{box-sizing:border-box;margin:0;padding:0}
html,body{width:1200px;height:2206px;overflow:hidden}
body{position:relative;background:#fff;font-family:"Oxygen",sans-serif;color:var(--text)}
.abs{position:absolute}

/* header */
.top-bar{left:0;top:0;width:1200px;height:38px;background:var(--bar);display:flex;justify-content:flex-end;align-items:center;gap:26px;padding-right:90px;font-size:12px;color:#ddd}
.main-nav{left:0;top:38px;width:1200px;height:71px;background:var(--nav);display:flex;justify-content:flex-end;align-items:center;gap:62px;padding-right:90px;font-family:"Montserrat",sans-serif;font-size:14px;color:#333}
.brand{left:87px;top:0;width:159px;height:109px;background:var(--ink);display:flex;flex-direction:column;align-items:center;justify-content:center;gap:6px;color:var(--gold);font-family:"Montserrat",sans-serif}
.brand .name{font-size:15px;letter-spacing:3px}
.brand .sub{font-size:8px;letter-spacing:2px}

/* hero */
.hero{left:0;top:109px;width:1200px;height:450px;background:linear-gradient(110deg,#2a1d14 0%,#5a3c25 55%,#a4713f 100%)}
.hero-title{left:84px;top:240px;font-family:"Montserrat",sans-serif;font-weight:700;font-size:64px;color:#fff;letter-spacing:4px}

/* promo banners */
.promo{top:498px;width:328px;height:249px;color:#fff;text-align:center;display:flex;flex-direction:column;align-items:center;justify-content:center}
.promo .tag{font-family:"Montserrat",sans-serif;font-size:15px;letter-spacing:3px}
.promo .pct{font-family:"Montserrat",sans-serif;font-weight:700;font-size:56px;letter-spacing:3px;border-bottom:1px solid #fff;padding-bottom:4px}
.promo .note{font-size:14px;margin-top:10px}

/* sidebar */
.filters{left:87px;top:771px;width:223px}
.filter-head{height:40px;background:var(--rust);color:#fff;font-family:"Montserrat",sans-serif;font-size:14px;padding:11px 16px;display:flex;justify-content:space-between}
.filter-list{list-style:none;background:var(--cream);padding:6px 16px 14px}
.filter-list li{font-size:13px;height:31px;display:flex;justify-content:space-between;align-items:center;color:#444}
.filter-list li::after{content:"+";color:#999}
.filter-block{margin-bottom:14px}

/* products */
.section-title{left:337px;top:778px;font-family:"Montserrat",sans-serif;font-size:23px;color:#333}
.sorters{left:835px;top:787px;display:flex;gap:32px;font-size:12px;color:#444}
.card{width:193px;height:368px;border:1px solid var(--line);background:#fff;text-align:center}
.card .photo{height:190px;margin:10px;background:radial-gradient(circle,#e8d6b4 0%,#f6f1e8 70%)}
.card .title{font-family:"Montserrat",sans-serif;font-size:14px;color:#333;margin-top:8px}
.card .price{font-size:13px;color:var(--gold);margin-top:4px}
.card .price s{color:#999;margin-left:6px}
.card .blurb{font-size:11px;line-height:1.45;padding:8px 14px 0;color:#777}
.card .actions{display:flex;justify-content:center;gap:8px;margin-top:12px}
.card .quick{width:106px;height:30px;background:#222;color:#fff;font-size:12px;display:flex;align-items:center;justify-content:center}
.card .wish{width:38px;height:30px;background:#222;display:flex;align-items:center;justify-content:center}
.load-more{left:646px;top:1603px;width:161px;height:51px;background:var(--rust);color:#fff;font-family:"Montserrat",sans-serif;font-size:14px;display:flex;align-items:center;justify-content:center;letter-spacing:1px}

/* footer */
.site-footer{left:0;top:1757px;width:1200px;height:449px;background:var(--footer);color:#bbb}
.footer-brand{left:87px;top:1830px;width:214px;text-align:center;color:#ddd;font-family:"Montserrat",sans-serif}
.footer-brand .mark{width:70px;height:70px;border:1px solid #ddd;margin:0 auto 18px}
.footer-brand .name{font-size:24px;letter-spacing:6px}
.footer-col{top:1808px;font-size:12px;line-height:2}
.footer-col h4,.footer-label{font-family:"Montserrat",sans-serif;font-size:15px;color:#eee;letter-spacing:1px;font-weight:600;margin-bottom:22px}
.social{left:87px;top:2060px;display:flex;gap:26px}
.social span{width:20px;height:20px;border-radius:50%;background:#ccc}
.news-input{left:631px;top:2053px;width:306px;height:51px;background:#fff;font-size:12px;color:#999;padding:17px 18px}
.news-submit{left:947px;top:2053px;width:168px;height:51px;background:#000;color:#fff;font-family:"Montserrat",sans-serif;font-size:14px;display:flex;align-items:center;justify-content:center}
.copyright{left:87px;top:2160px;font-size:12px;color:#aaa}
.payments{left:901px;top:2158px;display:flex;gap:10px}
.payments span{width:36px;height:24px;background:#ddd;border-radius:3px}

/* dim layer */
.veil{left:0;top:0;width:1200px;height:2206px;background:var(--veil)}

/* subscribe modal */
.modal{left:147px;top:107px;width:882px;height:424px;display:flex}
.modal-offer{width:485px;background:var(--gold);padding:44px 35px;color:#fff}
.modal-offer .enjoy{font-family:"Bebas Neue",sans-serif;font-size:52px;line-height:1;letter-spacing:1px}
.modal-offer .headline{font-family:"Bebas Neue",sans-serif;font-size:92px;line-height:1;margin-top:8px;letter-spacing:2px}
.modal-offer .copy{font-size:12.5px;line-height:1.55;margin-top:16px;width:390px}
.modal-offer .email{margin-top:18px;width:415px;height:50px;background:#fff;color:#888;font-size:12px;font-style:italic;padding:17px 28px}
.modal-offer .subscribe{margin-top:16px;width:164px;height:50px;background:#222;color:#fff;font-size:17px;display:flex;align-items:center;justify-content:center}
.modal-photo{flex:1;background:linear-gradient(160deg,#eadfcf 0%,#c49a6a 45%,#5a3520 100%)}
.modal-close{left:996px;top:78px;width:58px;height:58px;border-radius:50%;background:#fff;display:flex;align-items:center;justify-content:center}
</style>
</head>
<body>

<header>
  <div class="abs top-bar"><span>Sign In</span><span>Wishlist</span><span>My Cart</span><span>USD ▾</span>
    <svg width="14" height="14" viewBox="0 0 14 14"><circle cx="6" cy="6" r="4.5" fill="none" stroke="#ddd" stroke-width="1.6"/><line x1="9.3" y1="9.3" x2="13" y2="13" stroke="#ddd" stroke-width="1.6"/></svg>
  </div>
  <nav class="abs main-nav"><span>Home</span><span>Products</span><span>Our Story</span><span>FAQ</span><span>Blog</span><span>Contact Us</span></nav>
  <div class="abs brand"><span class="name">VELISTO</span><span class="sub">VELISTO JEWELLERY</span></div>
</header>

<main>
  <section class="abs hero" role="img" aria-label="Hero photograph of a woman wearing gold jewellery"></section>
  <div class="abs hero-title">BE BEAUTIFUL</div>

  <div class="abs promo" style="left:87px;background:linear-gradient(135deg,#6b4a2a,#2c1e12)" role="img" aria-label="Diamond rings promotion banner"><span class="tag">EXTRA</span><span class="pct">10% OFF</span><span class="note">Diamond rings till March 31st, 2018</span></div>
  <div class="abs promo" style="left:438px;background:linear-gradient(135deg,#8a6a3c,#3a2a18)" role="img" aria-label="Gold rings promotion banner"><span class="tag">EXTRA</span><span class="pct">20% OFF</span><span class="note">Gold rings till March 31st, 2018</span></div>
  <div class="abs promo" style="left:787px;background:linear-gradient(135deg,#2f3f5a,#141c2a)" role="img" aria-label="Silver rings promotion banner"><span class="tag">EXTRA</span><span class="pct">30% OFF</span><span class="note">Silver rings till March 31st, 2018</span></div>

  <aside class="abs filters">
    <div class="filter-block"><div class="filter-head">Category</div>
      <ul class="filter-list"><li>Ring</li><li>Necklace</li><li>Bracelet</li><li>Earring</li><li>Charms</li></ul></div>
    <div class="filter-block"><div class="filter-head">Collection</div>
      <ul class="filter-list"><li>Lorem Ipsum</li><li>Classic</li><li>Lorem Ipsum</li><li>Bridal</li><li>Lorem Ipsum</li></ul></div>
    <div class="filter-block"><div class="filter-head">Metal</div>
      <ul class="filter-list"><li>18K Rose Gold</li><li>14K Rose Gold</li><li>10K Rose Gold</li><li>18K Yellow Gold</li><li>14K Yellow Gold</li><li>10K Yellow Gold</li><li>18K White Gold</li><li>Silver Plated</li></ul></div>
    <div class="filter-head" style="margin-bottom:0;background:#7a3a20">Price <span>+</span></div>
    <div class="filter-head" style="background:var(--rust)">Gemstone <span>+</span></div>
  </aside>

  <h2 class="abs section-title">Product</h2>
  <div class="abs sorters"><span>Our Favourites ▾</span><span>What's New ▾</span><span>Price ▾</span></div>

  <div class="abs card" style="left:340px;top:831px"><div class="photo" role="img" aria-label="Silver ring with diamonds"></div><div class="title">Lorem Ipsum</div><div class="price">$ 99.90<s>$ 125.00</s></div><p class="blurb">Lorem ipsum is simply dummy text of the printing and typesetting industry.</p><div class="actions"><span class="quick">Quick View</span><span class="wish"><svg width="14" height="12" viewBox="0 0 14 12"><path d="M7 12 1.2 6A3.3 3.3 0 0 1 7 2a3.3 3.3 0 0 1 5.8 4Z" fill="#fff"/></svg></span></div></div>
  <div class="abs card" style="left:533px;top:831px"><div class="photo" role="img" aria-label="Sapphire ring"></div><div class="title">Lorem Ipsum</div><div class="price">$ 99.90<s>$ 125.00</s></div><p class="blurb">Lorem ipsum is simply dummy text of the printing and typesetting industry.</p><div class="actions"><span class="quick">Quick View</span><span class="wish"><svg width="14" height="12" viewBox="0 0 14 12"><path d="M7 12 1.2 6A3.3 3.3 0 0 1 7 2a3.3 3.3 0 0 1 5.8 4Z" fill="#fff"/></svg></span></div></div>
  <div class="abs card" style="left:726px;top:831px"><div class="photo" role="img" aria-label="Gold ring pair"></div><div class="title">Lorem Ipsum</div><div class="price">$ 99.90<s>$ 125.00</s></div><p class="blurb">Lorem ipsum is simply dummy text of the printing and typesetting industry.</p><div class="actions"><span class="quick">Quick View</span><span class="wish"><svg width="14" height="12" viewBox="0 0 14 12"><path d="M7 12 1.2 6A3.3 3.3 0 0 1 7 2a3.3 3.3 0 0 1 5.8 4Z" fill="#fff"/></svg></span></div></div>
  <div class="abs card" style="left:919px;top:831px"><div class="photo" role="img" aria-label="Rose gold ring"></div><div class="title">Lorem Ipsum</div><div class="price">$ 99.90<s>$ 125.00</s></div><p class="blurb">Lorem ipsum is simply dummy text of the printing and typesetting industry.</p><div class="actions"><span class="quick">Quick View</span><span class="wish"><svg width="14" height="12" viewBox="0 0 14 12"><path d="M7 12 1.2 6A3.3 3.3 0 0 1 7 2a3.3 3.3 0 0 1 5.8 4Z" fill="#fff"/></svg></span></div></div>

  <div class="abs card" style="left:340px;top:1213px"><div class="photo" role="img" aria-label="Gold earrings"></div><div class="title">Lorem Ipsum</div><div class="price">$ 99.90<s>$ 125.00</s></div><p class="blurb">Lorem ipsum is simply dummy text of the printing and typesetting industry.</p><div class="actions"><span class="quick">Quick View</span><span class="wish"><svg width="14" height="12" viewBox="0 0 14 12"><path d="M7 12 1.2 6A3.3 3.3 0 0 1 7 2a3.3 3.3 0 0 1 5.8 4Z" fill="#fff"/></svg></span></div></div>
  <div class="abs card" style="left:533px;top:1213px"><div class="photo" role="img" aria-label="Gold bangles"></div><div class="title">Lorem Ipsum</div><div class="price">$ 99.90<s>$ 125.00</s></div><p class="blurb">Lorem ipsum is simply dummy text of the printing and typesetting industry.</p><div class="actions"><span class="quick">Quick View</span><span class="wish"><svg width="14" height="12" viewBox="0 0 14 12"><path d="M7 12 1.2 6A3.3 3.3 0 0 1 7 2a3.3 3.3 0 0 1 5.8 4Z" fill="#fff"/></svg></span></div></div>
  <div class="abs card" style="left:726px;top:1213px"><div class="photo" role="img" aria-label="Silver ring with gemstone"></div><div class="title">Lorem Ipsum</div><div class="price">$ 99.90<s>$ 125.00</s></div><p class="blurb">Lorem ipsum is simply dummy text of the printing and typesetting industry.</p><div class="actions"><span class="quick">Quick View</span><span class="wish"><svg width="14" height="12" viewBox="0 0 14 12"><path d="M7 12 1.2 6A3.3 3.3 0 0 1 7 2a3.3 3.3 0 0 1 5.8 4Z" fill="#fff"/></svg></span></div></div>
  <div class="abs card" style="left:919px;top:1213px"><div class="photo" role="img" aria-label="Drop earrings"></div><div class="title">Lorem Ipsum</div><div class="price">$ 99.90<s>$ 125.00</s></div><p class="blurb">Lorem ipsum is simply dummy text of the printing and typesetting industry.</p><div class="actions"><span class="quick">Quick View</span><span class="wish"><svg width="14" height="12" viewBox="0 0 14 12"><path d="M7 12 1.2 6A3.3 3.3 0 0 1 7 2a3.3 3.3 0 0 1 5.8 4Z" fill="#fff"/></svg></span></div></div>

  <div class="abs load-more">LOAD MORE</div>
</main>

<footer>
  <div class="abs site-footer"></div>
  <div class="abs footer-brand"><div class="mark"></div><div class="name">VELISTO</div></div>
  <div class="abs footer-col" style="left:485px"><h4>ABOUT US</h4><div>Our Story</div><div>Wholesale Enquiry</div></div>
  <div class="abs footer-col" style="left:719px"><h4>SHOPPING</h4><div>Shop</div><div>Wishlist</div><div>Size Guide</div></div>
  <div class="abs footer-col" style="left:953px"><h4>CUSTOMER CARE</h4><div>Delivery</div><div>FAQs</div><div>Care &amp; Warranty</div><div>Contact Us</div></div>
  <div class="abs footer-label" style="left:90px;top:2002px">FOLLOW US</div>
  <div class="abs social"><span></span><span></span><span></span></div>
  <div class="abs footer-label" style="left:629px;top:2002px">NEWSLETTER SIGN UP</div>
  <div class="abs news-input">Your email</div>
  <div class="abs news-submit">SUBMIT</div>
  <div class="abs copyright">Copyright © 2018 Velisto Jewellery. All rights reserved.</div>
  <div class="abs payments"><span></span><span></span><span></span><span></span><span></span></div>
</footer>

<div class="abs veil"></div>

<section class="abs modal" aria-label="Newsletter offer">
  <div class="modal-offer">
    <div class="enjoy">ENJOY</div>
    <div class="headline">15 % OFF</div>
    <p class="copy">Lorem ipsum dolor sit amet, consectetur adipisicing elit,sed do eiusmod ut labore et dolore</p>
    <div class="email">Enter your email...</div>
    <div class="subscribe">SUBSCRIBE</div>
  </div>
  <div class="modal-photo" role="img" aria-label="Photograph of a bride in gold bridal jewellery and embroidered dress"></div>
</section>
<div class="abs modal-close" aria-label="Close">
  <svg width="20" height="20" viewBox="0 0 20 20"><path d="M3 3 17 17M17 3 3 17" stroke="#111" stroke-width="4" stroke-linecap="round"/></svg>
</div>

</body>
</html>
```